Der Flyer soll das Format DIN 105 lang haben und später bei druckfalter.de gedruckt werden. Entsprechende Vorlagen sind bei druckfalter.de vorhanden. Der Flyer wird in der Mitte 1x gefalzt und beidseitige bedruckt. (Es gibt also eine Außenseite, eine Doppel Innenseiten und eine Rückseite)
Der Flyer soll Neupatienten sowie BEstandspatienten ansprechen und über die Ärzte und die Leistungen informieren. Siehe www.praxis-lindenhof-beispiel.de
Die Fotos auf der Homepage können verwendet werden, entsprechende Lizenzen für die Nutzung liegen vor. An besseren Ideen bin ich natürlich auch interessiert :-)
Datenübergabe in Adobe Illustrator (.ai) oder Adobe InDesign (.indd)
Vielen Dank und beste Grüße

```html
<!DOCTYPE html>
<html lang="de">
<head>
<meta charset="utf-8">
<title>Praxis Lindenhof – Flyer DIN lang</title>
<link rel="stylesheet" href="https://fonts.googleapis.com/css2?family=Manrope:wght@300;400;500;600;700&display=swap">
<style>
  :root{
    --bg-top:#eef0f2;
    --bg-bottom:#e3e5e8;
    --navy:#1f2b3d;
    --ink:#2a3342;
    --muted:#4a5260;
    --sage:#c7d8db;
    --sage-soft:#d3e1e4;
    --sand:#e7d8ce;
    --paper:#ffffff;
    --paper-grey:#eef0f1;
    --rule:#9aa3ad;
  }
  *{margin:0;padding:0;box-sizing:border-box}
  html,body{width:1200px;height:900px;overflow:hidden}
  body{background:linear-gradient(180deg,var(--bg-top),var(--bg-bottom));font-family:"Manrope",sans-serif;color:var(--ink)}
  .stage{position:absolute;left:0;top:0;width:1152px;height:864px;transform:scale(1.0417);transform-origin:0 0}
  .abs{position:absolute}
  .panel{position:absolute;overflow:hidden}

  /* Titelseite */
  .cover{left:92px;top:90px;width:298px;height:683px;background:var(--sage)}
  .cover svg{position:absolute;left:0;top:0}
  .cover-brand{right:0;top:0;width:86px;height:88px;background:var(--paper);border-bottom-left-radius:60px;display:flex;align-items:center;justify-content:center;font-size:12px;font-weight:600;color:var(--navy)}
  .cover-title{left:25px;top:55px;font-size:35px;line-height:40px;font-weight:500;color:var(--navy);letter-spacing:-.5px}
  .cover-sub{left:25px;top:176px;font-size:26px;font-weight:300;color:var(--ink)}
  .cover-badge{left:26px;top:243px;width:82px;height:82px;border-radius:50%;background:var(--navy);color:#fff;display:flex;align-items:center;justify-content:center;text-align:center;font-size:14px;line-height:18px;font-weight:500}
  .cover-foot{top:602px;font-size:14px;line-height:19px;font-weight:500;color:var(--navy)}
  .cover-divider{left:143px;top:603px;width:1px;height:48px;background:var(--navy)}

  /* Innenseiten */
  .spread-left{left:452px;top:92px;width:305px;height:680px;background:var(--paper)}
  .spread-right{left:757px;top:92px;width:303px;height:680px;background:var(--paper-grey)}
  .spread-left svg,.spread-right svg{position:absolute;left:0;top:0}
  h2{font-size:22px;font-weight:600;color:var(--navy);letter-spacing:-.3px}
  .rule{height:1px;background:var(--rule)}
  .body{font-size:14px;line-height:19px;color:var(--muted)}
  .doctor-photo{width:74px;height:74px;border-radius:50%;background:radial-gradient(circle at 50% 40%,#d9c8bc,#b9c7cc 70%);border:2px solid #dfe6e8}
  .doctor-name{font-size:17px;font-weight:600;color:var(--navy)}
  .section-title{font-size:17px;font-weight:600;color:var(--navy)}

  .right-badge{left:212px;top:26px;width:68px;height:68px;border-radius:50%;background:var(--navy);color:#fff;display:flex;align-items:center;justify-content:center;text-align:center;font-size:11px;line-height:14px;font-weight:500}
  .lead{font-size:18px;color:var(--navy)}
  .service{left:22px;width:262px;height:55px;border-radius:28px;display:flex;align-items:center;padding-left:17px}
  .service.sand{background:var(--sand)} .service.sage{background:var(--sage)}
  .dots{display:grid;grid-template-columns:6px 6px;gap:5px;margin-right:18px}
  .dots i{width:6px;height:6px;border-radius:50%;background:var(--navy)}
  .service-col{font-size:10.5px;line-height:14px;color:var(--navy);width:70px}
  .service-col b{font-weight:600;display:block}
  .service-sep{width:1px;height:22px;background:var(--navy);margin:0 14px 0 8px}
  .contact{font-size:12.5px;line-height:21px;color:#fff}
  .contact strong{font-weight:700;font-size:13px;display:block;margin-top:14px}
</style>
</head>
<body>
<div class="stage">

  <section class="panel cover" aria-label="Titelseite">
    <svg width="298" height="683" viewBox="0 0 298 683">
      <defs>
        <linearGradient id="photoTone" x1="0" y1="0" x2="1" y2="1">
          <stop offset="0" stop-color="#e6e1dc"/>
          <stop offset=".5" stop-color="#9fb7c9"/>
          <stop offset="1" stop-color="#eceff1"/>
        </linearGradient>
      </defs>
      <path d="M0 292 L298 228 L298 520 L0 580 Z" fill="url(#photoTone)" role="img" aria-label="Foto: Praxisteam aus drei Ärztinnen und Ärzten in der Praxis"/>
      <path d="M0 580 L298 510 L298 683 L0 683 Z" fill="var(--sand)"/>
      <path d="M0 580 L298 510" stroke="#fff" stroke-width="6"/>
      <path d="M0 292 L298 228" stroke="#fff" stroke-width="5"/>
    </svg>
    <div class="abs cover-brand">Lindenhof</div>
    <div class="abs cover-title">Ihre<br>Hausarzt-<br>praxis</div>
    <div class="abs cover-sub">im Zentrum</div>
    <div class="abs cover-badge">Neue<br>Patienten</div>
    <div class="abs cover-foot" style="left:25px">Montag–Freitag<br>8–12 Uhr<br>15–18 Uhr</div>
    <div class="abs cover-divider"></div>
    <div class="abs cover-foot" style="left:166px">Termine<br>0123 555 0140<br>online buchbar</div>
  </section>

  <section class="panel spread-left" aria-label="Innenseite Ärzteteam">
    <svg width="305" height="680" viewBox="0 0 305 680">
      <path d="M0 500 Q150 525 305 502 L305 680 L0 680 Z" fill="var(--sage-soft)"/>
    </svg>
    <h2 class="abs" style="left:23px;top:36px">Unser Ärzteteam</h2>
    <div class="abs rule" style="left:23px;top:72px;width:100px"></div>
    <p class="abs body" style="left:23px;top:92px;width:270px">Wir begleiten Sie und Ihre Familie<br>mit Erfahrung, Zeit und offenem Ohr –<br>vom Check-up bis zur Nachsorge.</p>

    <div class="abs doctor-photo" style="left:23px;top:191px" role="img" aria-label="Porträtfoto Dr. Jonas Kessler"></div>
    <div class="abs doctor-name" style="left:109px;top:202px">Dr. Jonas Kessler</div>
    <p class="abs body" style="left:109px;top:226px">Facharzt für Allgemein-<br>medizin, hausärztliche<br>Versorgung</p>

    <div class="abs doctor-photo" style="left:23px;top:300px" role="img" aria-label="Porträtfoto Dr. Lea Brandt"></div>
    <div class="abs doctor-name" style="left:109px;top:305px">Dr. Lea Brandt</div>
    <p class="abs body" style="left:109px;top:329px">Fachärztin für Innere<br>Medizin, Diabetologie<br>und Vorsorge</p>

    <div class="abs doctor-photo" style="left:23px;top:404px" role="img" aria-label="Porträtfoto Dr. Tarek Sommer"></div>
    <div class="abs doctor-name" style="left:109px;top:409px">Dr. Tarek Sommer</div>
    <p class="abs body" style="left:109px;top:433px">Allgemeinmedizin,<br>Sportmedizin und<br>Reiseimpfungen</p>

    <div class="abs rule" style="left:23px;top:542px;width:252px;background:#7f8893"></div>
    <div class="abs section-title" style="left:23px;top:566px">Sprechzeiten</div>
    <p class="abs body" style="left:23px;top:593px">Mo, Di, Do<br>8–12, 15–18 Uhr<br>Mi, Fr 8–12 Uhr</p>
    <p class="abs body" style="left:156px;top:593px">Akutsprechstunde<br>täglich 8–9 Uhr<br>ohne Termin</p>
  </section>

  <section class="panel spread-right" aria-label="Innenseite Leistungen und Kontakt">
    <svg width="303" height="680" viewBox="0 0 303 680">
      <path d="M186 0 L303 0 L303 130 L240 130 Q186 130 186 76 Z" fill="var(--sage)"/>
      <path d="M0 500 Q150 512 303 478 L303 680 L0 680 Z" fill="var(--sage-soft)"/>
      <path d="M0 500 Q60 506 120 504 L120 580 L0 600 Z" fill="#dbe6e8" role="img" aria-label="Kartenausschnitt mit Anfahrt zur Praxis"/>
      <path d="M112 680 Q112 520 200 498 Q250 486 303 478 L303 680 Z" fill="var(--navy)"/>
    </svg>
    <div class="abs right-badge">Praxis<br>Mitte</div>
    <div class="abs" style="left:22px;top:42px;font-size:18px;color:var(--ink)">Leistungen</div>
    <div class="abs rule" style="left:22px;top:74px;width:110px"></div>
    <div class="abs lead" style="left:22px;top:98px;font-weight:600">Für Sie</div>
    <div class="abs lead" style="left:22px;top:125px;font-weight:500">von Vorsorge bis Akut</div>
    <div class="abs" style="left:22px;top:151px;font-size:16px;color:var(--muted)">unser Angebot.</div>

    <div class="abs service sand" style="top:203px"><span class="dots"><i></i><i></i><i></i><i></i></span><span class="service-col"><b>Vorsorge</b>Check-up</span><span class="service-sep"></span><span class="service-col"><b>Impfung</b>Reise</span></div>
    <div class="abs service sand" style="top:266px"><span class="dots"><i></i><i></i><i></i><i></i></span><span class="service-col"><b>Labor</b>Blutbild</span><span class="service-sep"></span><span class="service-col"><b>EKG</b>Ruhe-EKG</span></div>
    <div class="abs service sage" style="top:328px"><span class="dots"><i></i><i></i><i></i><i></i></span><span class="service-col"><b>Ultraschall</b>Bauch</span><span class="service-sep"></span><span class="service-col"><b>Hausbesuch</b>nach Absprache</span></div>
    <div class="abs service sand" style="top:391px"><span class="dots"><i></i><i></i><i></i><i></i></span><span class="service-col"><b>Beratung</b>Ernährung</span><span class="service-sep"></span><span class="service-col"><b>DMP</b>Diabetes</span></div>

    <div class="abs" style="left:21px;top:611px;font-size:9px;line-height:10px;font-weight:600;color:var(--navy)">Anfahrt<br>Parkplätze</div>
    <div class="abs" style="left:21px;top:636px;font-size:13px;color:var(--navy)">Bus 22</div>

    <div class="abs contact" style="left:161px;top:522px">
      Kontakt &amp; Termine
      <div class="rule" style="width:118px;background:#8b95a3;margin-top:6px"></div>
      <strong>PRAXIS LINDENHOF</strong>
      Lindenweg 12<br>12345 Musterstadt<br>Tel. 0123 555 0140
    </div>
  </section>

</div>
</body>
</html>
```